Velmarotix - world unique technology for better life - please let them know who am i at first sight

We need a new business card for company which is a provider of unique crystal based technology suitable for all living being. For more information and final design you can use our brochure (our colours are black and blue from brochure).
We use Verdana font

Industry/Entity Type

Business

Contact Information for Business Card

regular dimension

Font styles to use
Other font styles liked:
• Verdana

Requirements
Must have
• Logo
• name
• function/position
• phone
• mobile
• e-mail
• adress
Nice to have
• inovative design (technology directed)

```html
<!DOCTYPE html>
<html lang="en">
<head>
<meta charset="utf-8">
<title>Velmarotix Technologies – Business Card</title>
<link rel="stylesheet" href="https://fonts.googleapis.com/css2?family=Open+Sans:wght@300;400;700&display=swap">
<style>
  :root {
    --ink: #050607;
    --paper: #ffffff;
    --brand-blue: #1aa3e6;
    --brand-blue-deep: #0f4f73;
    --halo: #0b2433;
    --text-light: #e9eef2;
    --stage: #d9dcdf;
  }
  * { margin: 0; padding: 0; box-sizing: border-box; }
  html, body { width: 1200px; height: 948px; overflow: hidden; }
  body {
    background: var(--stage);
    font-family: "Open Sans", Verdana, sans-serif;
    display: flex;
    flex-direction: column;
    align-items: center;
    justify-content: center;
    gap: 40px;
  }
  .card {
    width: 760px;
    height: 434px;
    position: relative;
    overflow: hidden;
    box-shadow: 0 6px 18px rgba(0,0,0,0.18);
  }

  /* Front */
  .card-front { background: var(--ink); color: var(--text-light); }
  .brand {
    position: absolute; left: 48px; top: 44px;
    display: flex; align-items: center; gap: 22px;
  }
  .brand-dot {
    width: 84px; height: 84px; border-radius: 50%;
    background: var(--brand-blue);
  }
  .brand-name {
    font-size: 54px; font-weight: 400; letter-spacing: 1px;
    color: var(--brand-blue); line-height: 1;
  }
  .brand-tagline {
    position: absolute; left: 154px; top: 128px;
    font-size: 19px; font-weight: 300; letter-spacing: 9px;
    color: var(--brand-blue);
  }
  .contacts {
    position: absolute; left: 52px; top: 190px;
    list-style: none; font-size: 15px; line-height: 30px;
  }
  .contacts li { display: flex; align-items: center; gap: 12px; }
  .contacts svg { width: 16px; height: 16px; fill: var(--brand-blue); }
  .address {
    position: absolute; left: 52px; bottom: 40px;
    font-size: 15px; color: var(--text-light);
  }
  .halo {
    position: absolute; right: 40px; bottom: 26px;
    width: 250px; height: 250px; border-radius: 50%;
    background: var(--halo);
  }
  .person {
    position: absolute; right: 60px; bottom: 118px; text-align: left;
  }
  .person-name {
    font-size: 27px; font-weight: 700; color: var(--brand-blue);
  }
  .person-role { font-size: 19px; color: var(--text-light); margin-top: 4px; }

  /* Back */
  .card-back { background: var(--paper); }
  .back-mark {
    position: absolute; left: 50%; top: 46%;
    transform: translate(-50%, -50%);
    display: flex; align-items: center; gap: 20px;
  }
  .back-dot {
    width: 120px; height: 120px; border-radius: 50%;
    background: var(--brand-blue);
  }
  .back-name { font-size: 48px; color: var(--brand-blue); letter-spacing: 1px; }
  .web {
    position: absolute; left: 44px; bottom: 34px;
    font-size: 18px; font-weight: 700; letter-spacing: 3px;
    color: #1c1c1c;
  }
</style>
</head>
<body>
  <section class="card card-front">
    <div class="brand">
      <span class="brand-dot"></span>
      <span class="brand-name">VELMAROTIX</span>
    </div>
    <div class="brand-tagline">TECHNOLOGIES</div>

    <ul class="contacts">
      <li>
        <svg viewBox="0 0 16 16"><path d="M3 1h3l1.5 4-2 1.2a9 9 0 0 0 4.3 4.3L11 8.5l4 1.5v3a2 2 0 0 1-2 2A12 12 0 0 1 1 3a2 2 0 0 1 2-2z"/></svg>
        012-345-6789
      </li>
      <li>
        <svg viewBox="0 0 16 16"><path d="M4 0h8a1 1 0 0 1 1 1v14a1 1 0 0 1-1 1H4a1 1 0 0 1-1-1V1a1 1 0 0 1 1-1zm1 2v10h6V2zm3 11a1 1 0 1 0 0 2 1 1 0 0 0 0-2z"/></svg>
        012-345-6789
      </li>
      <li>
        <svg viewBox="0 0 16 16"><path d="M1 3h14v10H1zm1.5 1.2V12h11V4.2L8 8.5z M2.8 4 8 7.4 13.2 4z"/></svg>
        mail@velmarotix.com
      </li>
      <li>
        <svg viewBox="0 0 16 16"><circle cx="8" cy="8" r="7" fill="none" stroke="#1aa3e6" stroke-width="1.5"/><path d="M1 8h14M8 1c-3 4-3 10 0 14M8 1c3 4 3 10 0 14" fill="none" stroke="#1aa3e6" stroke-width="1.2"/></svg>
        www.velmarotix.cu
      </li>
    </ul>

    <p class="address">Street Name, City Name, Zipcode-01234</p>

    <div class="halo"></div>
    <div class="person">
      <p class="person-name">Mira Kostelic</p>
      <p class="person-role">Founder and CEO</p>
    </div>
  </section>

  <section class="card card-back">
    <div class="back-mark">
      <span class="back-dot"></span>
      <span class="back-name">VELMAROTIX</span>
    </div>
    <p class="web">www.velmarotix.cu</p>
  </section>
</body>
</html>
```